Flyer Design for Coastal Guild of Reflective Counsellors and Psychotherapists (CGRCP)

We need a new flyer designed for CGRCP. We want to attract new members @ a tradeshow. Counsellors and Psychotherapists looking for a professional association with which to align themselves where they feel @ home because they share similar values.We would like to use the colours and leaves from our website which is www.cgrcp-guild.org if possible or similar colours and the photo of the tree in bloom from Facebook "stillwaterandmindwork". As well as our logo (www.cgrcp-guild.org), the TRELMO (www.trelmo-hub.org) logo as well somewhere in the bottom corner the Harbour Circle logo (www.harbourcirclenet.org).
Updates

Target Market(s)

Psychotherapists and Counsellors

Industry/Entity Type

Mental Health

Colors
876aae
b7a5cd
e4daeb
cadf82
abd036
9bcb3b

Requirements
Must have
• Logo
Nice to have
• Warm inviting photo of lotus flower
Should not have
• No monks

```html
<!DOCTYPE html>
<html lang="en">
<head>
<meta charset="utf-8">
<title>CGRCP Flyer</title>
<link href="https://fonts.googleapis.com/css2?family=Open+Sans:wght@300;400;600;700&display=swap" rel="stylesheet">
<style>
  :root {
    --stage: #ededed;
    --paper: #ffffff;
    --lilac-deep: #876aae;
    --lilac-mid: #b7a5cd;
    --lilac-pale: #e4daeb;
    --lilac-text: #9580b6;
    --ink: #1a1a1a;
    --cover-top: #cbbcd3;
    --photo-warm: #b3385f;
    --photo-deep: #7e2a45;
    --band: rgba(196, 176, 210, 0.82);
  }
  * { box-sizing: border-box; margin: 0; padding: 0; }
  html, body { width: 1200px; height: 900px; overflow: hidden; }
  body {
    background: var(--stage);
    font-family: "Open Sans", Arial, sans-serif;
    position: relative;
  }

  /* Cover page */
  .cover {
    position: absolute; left: 72px; top: 90px; width: 486px; height: 724px;
    background: linear-gradient(180deg, var(--cover-top) 0%, #c6b3cb 40%, #c9b5cb 45%);
    overflow: hidden;
  }
  .cover-title {
    position: absolute; top: 48px; width: 100%; text-align: center;
    font-weight: 300; font-size: 56px; color: #fff; letter-spacing: 1px;
  }
  .cover-mark {
    position: absolute; left: 203px; top: 128px; width: 80px; height: 80px;
    border-radius: 50%; background: #fff; opacity: 0.9;
  }
  .cover-photo {
    position: absolute; left: 0; top: 250px; width: 100%; height: 474px;
    background:
      linear-gradient(180deg, rgba(203,188,211,1) 0%, rgba(203,188,211,0) 28%),
      radial-gradient(ellipse at 60% 60%, #d24a74 0%, var(--photo-warm) 45%, var(--photo-deep) 100%);
  }
  .cover-band {
    position: absolute; left: 0; top: 656px; width: 100%; height: 40px;
    background: var(--band);
    color: #fff; font-weight: 600; font-size: 14.5px;
    display: flex; align-items: center; justify-content: center;
  }

  /* Info page */
  .info {
    position: absolute; left: 615px; top: 90px; width: 515px; height: 724px;
    background: var(--paper); overflow: hidden;
  }
  .leaf-wash {
    position: absolute; border-radius: 60% 40% 55% 45%;
    background: radial-gradient(circle at 40% 40%, var(--lilac-pale), rgba(228,218,235,0));
  }
  .leaf-wash.top { left: -20px; top: -30px; width: 300px; height: 190px; }
  .leaf-wash.side { left: 420px; top: 500px; width: 140px; height: 200px; }
  .info-name {
    position: absolute; left: 82px; top: 38px;
    font-weight: 400; font-size: 31px; color: var(--ink); letter-spacing: 0.5px;
  }
  .info-mark {
    position: absolute; left: 123px; top: 86px; width: 50px; height: 50px;
    border-radius: 50%; background: var(--ink);
  }
  .col { position: absolute; width: 222px; }
  .col.left { left: 31px; top: 164px; }
  .col.right { left: 269px; top: 40px; }
  h2 {
    font-weight: 400; font-size: 21px; color: var(--ink);
    line-height: 28px; margin-bottom: 6px;
  }
  p, li {
    font-size: 10.5px; line-height: 12.1px; color: var(--lilac-text);
    letter-spacing: -0.15px;
    text-align: left;
    hyphens: auto; -webkit-hyphens: auto;
  }
  .objectives p { margin-bottom: 12.5px; }
  .objectives { margin-bottom: 2px; }
  .next-training {
    font-weight: 600; font-size: 13px; line-height: 15px; letter-spacing: 0;
    color: var(--lilac-deep); margin: 12px 0 6px;
  }
  .goals { list-style: none; }
  .goals li { text-align: justify; text-align-last: left; }
  .goals li::before { content: "• "; }
  .footer-rule {
    position: absolute; left: 31px; right: 31px; top: 673px;
    border-top: 1px solid var(--lilac-mid);
  }
  .footer-url {
    position: absolute; right: 28px; top: 683px;
    font-size: 10.5px; color: var(--ink);
  }
</style>
</head>
<body>

<section class="cover">
  <h1 class="cover-title">CGRCP</h1>
  <div class="cover-mark" aria-hidden="true"></div>
  <div class="cover-photo" role="img" aria-label="Warm photograph of smiling counsellors gathered together in red robes"></div>
  <div class="cover-band">Coastal Guild of Reflective Counsellors and Psychotherapists</div>
</section>

<section class="info">
  <div class="leaf-wash top" role="img" aria-label="Soft lilac leaf decoration"></div>
  <div class="leaf-wash side" role="img" aria-label="Soft lilac leaf decoration"></div>

  <div class="info-name">CGRCP</div>
  <div class="info-mark" aria-hidden="true"></div>

  <div class="col left">
    <h2>Our Vision</h2>
    <p>The purpose of The Coastal Guild of Reflective Counsellors and Psychotherapists (CGRCP), a TRELMO Member Association, is to bring the whole philosophy and practice of Buddhism (the dhamma), to therapists and counsellors, using innovative educational experiences.</p>
    <p>The benefits of introducing Buddhist practices into mental health is now scientifically validated, as increasing the effectiveness of Western psychotherapeutic approaches, as well as taking care of therapists in particular ‘burnout.’</p>
    <p>There is much to benefit us, as well as those we work with, in our desire to integrate Psychotherapy with Buddhism. So, CGRCP has developed and has been running a two-year professional training course in Buddhism and Psychotherapy, since 2008.</p>
    <p class="next-training">The next training will begin July 2016.</p>
    <h2>Some of Our Values</h2>
    <p>We care about therapists</p>
    <p>We strive to be of service to our members and all those we come into contact with humility, fairness, patience and compassion</p>
    <p>We value the ongoing need for education for therapists but we also value the balance between the mind, the body and the spirit, knowing that all those need to be nourished</p>
    <p>We work in warm, generous, spirited partnership with others and we are open to working within and across sectors to influence and co-develop initiatives.</p>
  </div>

  <div class="col right">
    <h2>CGRCP’s Objectives</h2>
    <div class="objectives">
      <p>To provide a philosophical base, standards, and ethics for the practice of Buddhist Counselling and Psychotherapy;</p>
      <p>Maintain unique professional development of its members, as well as provide a warm and supportive community of therapists.</p>
      <p>Develop a professional organisational structure that supports the practice of Buddhist Counselling and Psychotherapy;</p>
      <p>Provide an innovative education, training and research in Buddhist Counselling and Psychotherapy;</p>
      <p>Promote Buddhist Counselling and Psychotherapy in the community;</p>
      <p>Provide accreditation practices that will support the highest quality practice in Buddhist Counselling and Psychotherapy; and</p>
      <p>Work collaboratively and beneficially with other Buddhist and Counselling and Psychotherapy Organisations.</p>
    </div>
    <h2>Our Goals</h2>
    <ul class="goals">
      <li>To present Buddhism in a thorough way</li>
      <li>To explore and discuss dhamma and how it can improve the effectiveness of a thera&shy;pist’s life</li>
      <li>To provide ongoing education in all as&shy;pects of Buddhism for mental health pro&shy;fessionals</li>
      <li>To develop a dynamic organisation that stays attuned to changes in Buddhism as it is expressed in the West</li>
      <li>To develop a strong member&shy;ship/com&shy;munity</li>
      <li>To develop a relevant and important voice in the community</li>
      <li>To develop a unique professional identity</li>
      <li>To encourage positive social change</li>
    </ul>
  </div>

  <div class="footer-rule"></div>
  <div class="footer-url">www.stillwaterandmindwork.org</div>
</section>

</body>
</html>
```